Boutique town planning business needs a Business Card design

We need a business card design for a new company called The Zoning Bridgeway. We provide town planning and urban design services to government, business and community groups. We would like to see the designs use the colours in the logo (blue, deep red, green and amber), plenty of white and including black and grey in the writing. The final design should communicate collaboration, creativity and professionalism and that we are approachable.

Industry/Entity Type

Town

```html
<!DOCTYPE html>
<html lang="en">
<head>
<meta charset="utf-8">
<title>The Zoning Bridgeway – Business Card</title>
<link rel="stylesheet" href="https://fonts.googleapis.com/css2?family=Open+Sans:wght@400;700&family=Cinzel:wght@600&display=swap">
<style>
  :root{
    --bg:#d9d6d1;
    --card-white:#f3f3f3;
    --card-black:#0c0c0c;
    --ink:#3a3a3a;
    --ink-soft:#6b6b6b;
    --grey-light:#b9b9b9;
    --red:#a3302a;
    --amber:#d8951f;
    --green:#6aa83a;
    --blue:#4c9cc7;
  }
  *{box-sizing:border-box;margin:0;padding:0}
  html,body{width:1200px;height:900px;overflow:hidden}
  body{background:var(--bg);font-family:"Open Sans",Arial,sans-serif;position:relative}
  .card{position:absolute;width:640px;height:390px;left:280px;overflow:hidden;box-shadow:0 6px 18px rgba(0,0,0,.18)}
  .card--back{top:40px;background:var(--card-black)}
  .card--front{top:470px;background:var(--card-white)}

  .brand{position:absolute;display:flex;align-items:center;gap:14px}
  .brand__dot{width:46px;height:46px;border-radius:50%;background:var(--blue);flex:none}
  .brand__name{font-weight:700;font-size:26px;line-height:1;letter-spacing:-.3px}
  .card--back .brand{left:70px;top:70px}
  .card--back .brand__name{color:var(--grey-light)}
  .card--front .brand{left:60px;top:50px}
  .card--front .brand__name{color:var(--ink)}

  .faint-circle{position:absolute;right:-70px;top:120px;width:330px;height:330px;border-radius:50%;background:#1a1a1a}

  .contact{position:absolute;left:300px;top:170px;color:var(--ink-soft);font-size:13px;line-height:1.45}
  .contact__name{font-family:"Cinzel",Georgia,serif;font-size:17px;color:var(--ink);letter-spacing:.5px}
  .contact__role{font-size:11.5px}
  .contact__list{list-style:none;margin-top:12px}
  .contact__list li{display:flex;gap:14px}
  .contact__key{font-weight:700;width:10px}
  .key-m{color:var(--red)} .key-e{color:var(--amber)} .key-w{color:var(--red)}

  .footer-band{position:absolute;left:0;bottom:0;width:640px;height:70px}
  .abn{position:absolute;left:360px;bottom:18px;color:var(--grey-light);font-size:13px;letter-spacing:.5px}
</style>
</head>
<body>
  <section class="card card--back" aria-label="Card back">
    <div class="faint-circle" aria-hidden="true"></div>
    <div class="brand">
      <span class="brand__dot" aria-hidden="true"></span>
      <span class="brand__name">The Zoning Bridgeway</span>
    </div>
  </section>

  <section class="card card--front" aria-label="Card front">
    <div class="brand">
      <span class="brand__dot" aria-hidden="true"></span>
      <span class="brand__name">The Zoning Bridgeway</span>
    </div>

    <div class="contact">
      <p class="contact__name">Maren Holloway</p>
      <p class="contact__role">BPD (Urban Planning), GDipPD, MPIA, YPELA</p>
      <p class="contact__role">Director</p>
      <ul class="contact__list">
        <li><span class="contact__key key-m">M</span>0412 555 038</li>
        <li><span class="contact__key key-e">E</span>hello@zoningbridgeway.com.au</li>
        <li><span class="contact__key key-w">W</span>www.zoningbridgeway.com.au</li>
      </ul>
    </div>

    <svg class="footer-band" viewBox="0 0 640 70" aria-hidden="true">
      <rect x="0" y="62" width="50" height="8" fill="var(--red)"/>
      <rect x="50" y="62" width="50" height="8" fill="var(--amber)"/>
      <rect x="100" y="62" width="50" height="8" fill="var(--green)"/>
      <rect x="150" y="62" width="50" height="8" fill="var(--blue)"/>
      <polygon points="200,62 200,70 640,70 640,20 250,20" fill="var(--card-black)"/>
    </svg>
    <p class="abn">ABN 51824753106</p>
  </section>
</body>
</html>
```